Brenwick Structures Construction Company Seeking Modern Website

We are a small construction company wanting to create a web presence. We don't have much in the way of current content but will get photos as they come in. Attached is a picture of our business card.
The pages we would like on the menu are:
Home
Portfolio
Product Specs
Testimonials
Our Process
Contact
Some designs we like are:
http://www.tovasheds-example.com/
http://www.qrnstructures-example.com/
http://dunholtbarns-example.com/
http://pellingframes-example.com/
Not much requirements other than that so feel free to be creative!
Updates
Target Market(s)
Construction
Commercial and Residential Buildings
Industry/Entity Type
Construction Company
Number of Pages Required
5+ page
Look and feel

```html
<!DOCTYPE html>
<html lang="en">
<head>
<meta charset="utf-8">
<title>Brenwick Structures</title>
<link rel="stylesheet" href="https://fonts.googleapis.com/css2?family=Lato:ital,wght@0,400;0,700;1,400;1,700&display=swap">
<style>
:root{
  --blue:#1ea0d8;
  --red:#d9302a;
  --ink:#3a3a3a;
  --muted:#6c6c72;
  --line:#e2e2e2;
  --band:#ececec;
  --footer:#2f2f2f;
}
*{margin:0;padding:0;box-sizing:border-box}
html,body{width:882px;height:1200px;overflow:hidden;background:#fff}
body{position:relative;font-family:'Lato',sans-serif;color:var(--ink)}
.abs{position:absolute}
.top-rule{left:0;top:0;width:882px;height:3px;background:var(--blue)}
.brand{left:96px;top:22px;font-family:'Lato',sans-serif;font-weight:700;font-size:26px;color:var(--blue);display:flex;align-items:center;gap:8px}
.brand .dot{width:14px;height:14px;border-radius:50%;background:var(--red)}
.callout{right:96px;top:30px;display:flex;align-items:center;gap:8px;font-size:14px}
.callout em{color:var(--muted);font-style:italic;font-weight:700;margin-right:4px}
.callout .phone{color:var(--blue);font-weight:700;font-size:13px}
.nav{left:0;top:77px;width:882px;height:35px;border-top:1px solid var(--line);border-bottom:1px solid var(--line)}
.nav ul{position:absolute;left:96px;top:8px;width:690px;display:flex;list-style:none}
.nav li{flex:1;text-align:center;font-size:11px;color:var(--muted);border-left:1px solid var(--line);line-height:18px}
.nav li:last-child{border-right:1px solid var(--line)}
.nav li.active{color:var(--red)}
.hero{left:0;top:112px;width:882px;height:332px;background:linear-gradient(180deg,#8fc8ee 0%,#c9d6d8 35%,#7fb34a 62%,#4f8f22 100%)}
.hero-curve{left:0;top:380px}
.tagline{right:112px;top:306px;text-align:right;font-style:italic;font-size:28px;line-height:39px;color:#fff;text-shadow:0 1px 3px rgba(0,0,0,.4)}
.dots{left:416px;top:416px;display:flex;gap:6px}
.dots span{width:8px;height:8px;border-radius:50%;background:rgba(255,255,255,.7)}
.dots span.on{background:var(--red)}
.welcome{left:0;top:478px;width:882px;text-align:center;font-size:22px;color:var(--muted);letter-spacing:.3px}
.welcome b{color:var(--blue);font-weight:400}
.intro{left:108px;top:518px;width:666px;text-align:center;font-size:11.2px;line-height:15.6px;color:var(--muted)}
.read-more{left:0;top:584px;width:882px;text-align:center;font-size:11px;font-weight:700;color:var(--blue)}
.card{top:638px;width:213px;height:222px;background:#fff;border:1px solid var(--line);border-top:3px solid var(--blue);box-shadow:0 8px 8px -6px rgba(0,0,0,.18)}
.card h3{position:absolute;left:46px;top:14px;font-size:14.5px;font-weight:400;color:var(--blue)}
.card .icon{position:absolute;left:10px;top:10px;width:28px;height:28px;border-radius:50%;background:var(--red)}
.news{position:absolute;left:10px;width:191px;height:52px;border-bottom:1px dashed #cfcfcf}
.news:last-of-type{border-bottom:none}
.date{position:absolute;left:0;top:0;width:27px;height:29px;background:#3a3a3a;color:#fff;text-align:center;font-size:11px;font-weight:700;line-height:15px;border-radius:2px}
.date small{display:block;font-size:6.5px;line-height:11px;background:#555;font-weight:700}
.news h4,.task h4{font-size:9.6px;font-weight:700;color:#333}
.news p,.task p{font-size:8.8px;line-height:13px;color:#555}
.news .txt{position:absolute;left:34px;top:-2px}
.link{position:absolute;font-size:9px;font-weight:700;color:var(--blue)}
.task{position:absolute;left:10px;width:195px}
.task .tick{position:absolute;left:0;top:1px}
.task .txt{position:absolute;left:20px;top:0;width:175px}
.task h4{font-size:10.8px;font-weight:400;color:#333}
.avatar{position:absolute;left:10px;top:48px;width:64px;height:64px;border-radius:50%;border:3px solid var(--blue);background:linear-gradient(160deg,#d7dfe4,#8a9aa6)}
.person{position:absolute;left:86px;top:68px}
.person b{display:block;font-size:11.5px;font-weight:400;color:#333}
.person small{font-size:9px;color:#555}
.quote{position:absolute;left:10px;top:130px;width:193px;height:77px;border:1px solid var(--line);padding:8px 10px;font-style:italic;font-size:10px;line-height:16.5px;color:#444}
.qdots{position:absolute;right:12px;bottom:6px;display:flex;gap:3px}
.qdots span{width:5px;height:5px;border-radius:50%;background:#ccc}
.qdots span.on{background:var(--red)}
.types{left:0;top:894px;width:882px;height:200px;background:var(--band)}
.types-tab{left:352px;top:894px}
.types-title{left:352px;top:898px;width:176px;text-align:center;font-size:15px;color:#fff;font-weight:400}
.tile{top:946px;width:164px;height:118px;border:2px solid #fff;box-shadow:0 1px 3px rgba(0,0,0,.15)}
.tile .label{position:absolute;left:0;bottom:0;width:100%;height:19px;background:rgba(30,160,216,.85);color:#fff;text-align:center;font-size:12px;line-height:19px}
.arrow{top:995px}
.footer{left:0;top:1094px;width:882px;height:106px;background:var(--footer)}
.footer-brand{left:0;top:1110px;width:882px;text-align:center;font-size:20px;font-weight:700;color:var(--blue)}
.footer-nav{left:0;top:1152px;width:882px;display:flex;justify-content:center;list-style:none}
.footer-nav li{font-size:9px;color:#fff;font-weight:700;padding:0 8px;border-left:1px solid #555;line-height:11px}
.footer-nav li:first-child{border-left:none;color:var(--blue);font-weight:400}
.copy{left:0;top:1177px;width:882px;text-align:center;font-size:8.5px;color:#bbb}
.bottom-rule{left:0;top:1197px;width:882px;height:3px;background:var(--blue)}
</style>
</head>
<body>
<div class="abs top-rule"></div>

<header>
  <div class="abs brand"><span class="dot"></span>Brenwick Structures</div>
  <div class="abs callout"><em>Call us TODAY !</em>
    <svg width="12" height="12" viewBox="0 0 24 24"><path fill="#1ea0d8" d="M6.6 10.8a15 15 0 0 0 6.6 6.6l2.2-2.2c.3-.3.7-.4 1-.2 1.1.4 2.3.6 3.6.6.6 0 1 .4 1 1V20c0 .6-.4 1-1 1A17 17 0 0 1 3 4c0-.6.4-1 1-1h3.5c.6 0 1 .4 1 1 0 1.3.2 2.5.6 3.6.1.3 0 .7-.2 1z"/></svg>
    <span class="phone">+1 555 014 2290</span></div>
  <nav class="abs nav"><ul>
    <li class="active">HOME</li><li>PORTFOLIO</li><li>PRODUCT SPECS</li><li>TESTIMONIALS</li><li>OUR PROCESS</li><li>CONTACT US</li>
  </ul></nav>
</header>

<section>
  <div class="abs hero" role="img" aria-label="Photo of a smiling family sitting on a lawn in front of a house"></div>
  <svg class="abs hero-curve" width="882" height="70" viewBox="0 0 882 70">
    <path d="M0 12 Q441 96 882 12 L882 70 L0 70 Z" fill="#fff"/>
    <path d="M0 12 Q441 96 882 12 Q441 78 0 12 Z" fill="#d9302a"/>
  </svg>
  <div class="abs tagline">Building Dreams, So You Can<br>Build Memories</div>
  <div class="abs dots"><span class="on"></span><span></span><span></span><span></span></div>
</section>

<section>
  <h1 class="abs welcome">WELCOME TO <b>BRENWICK STRUCTURES</b></h1>
  <p class="abs intro">Lorem ipsum dolor sit amet, consectetur adipiscing elit. Praesent volutpat ultricies euismod. Mauris consectetur tellus quis sem dictum pharetra. Nullam euismod nunc blandit mi sagittis, et posuere nunc iaculis. Aenean in sollicitudin quam, non accumsan ipsum. Vivamus in aliquet ex. Nullam malesuadammodo mi, tristique faucibus nisl condimentum condimentum. Duis porttitor nisi ut elementum so</p>
  <div class="abs read-more">READ MORE</div>
</section>

<section>
  <div class="abs card" style="left:96px">
    <span class="icon"></span>
    <svg class="abs" style="left:17px;top:17px" width="14" height="14" viewBox="0 0 14 14"><path fill="#fff" d="M1 5h3l6-4v12L4 9H1z"/></svg>
    <h3>LATEST NEWS</h3>
    <div class="news" style="top:50px"><div class="date">22<small>JULY</small></div><div class="txt"><h4>Vero eros accumsaet odio</h4><p>quis nostrud exetiperj suscipit lobtis<br>nisl ut aliquip ex ea commod</p></div></div>
    <div class="news" style="top:101px"><div class="date">22<small>JULY</small></div><div class="txt"><h4>Eros accumsaet iusto odio</h4><p>quis nostrud exetiperj suscipit lobtfis<br>nisl ut aliquip exea commod</p></div></div>
    <div class="news" style="top:155px"><div class="date">22<small>JULY</small></div><div class="txt"><h4>Croeros accumsaet iusto odio</h4><p>quis nostrud exetiperj suscipit lobtisf<br>nisl ut aliquip ex commod</p></div></div>
    <span class="link" style="left:137px;top:200px">READ MORE ⊕</span>
  </div>

  <div class="abs card" style="left:334px">
    <span class="icon"></span>
    <svg class="abs" style="left:17px;top:17px" width="14" height="14" viewBox="0 0 14 14"><rect x="1" y="2" width="12" height="11" fill="none" stroke="#fff" stroke-width="1.5"/><path stroke="#fff" stroke-width="1.5" d="M1 5h12"/></svg>
    <h3>WHAT WE DO</h3>
    <div class="task" style="top:48px"><svg class="tick" width="11" height="10" viewBox="0 0 11 10"><path d="M1 5l3 3 6-7" fill="none" stroke="#5a8f8a" stroke-width="2"/></svg><div class="txt"><h4>Vulputate Molestie Consequat</h4><p>quis nostrud exsetiperj aliquip commod consequa uisquis nostru suscipit nisl roli aliquip exea commod</p></div></div>
    <span class="link" style="left:150px;top:108px">KNOW MORE</span>
    <div class="abs" style="left:10px;top:124px;width:192px;border-top:1px dashed #cfcfcf"></div>
    <div class="task" style="top:133px"><svg class="tick" width="11" height="10" viewBox="0 0 11 10"><path d="M1 5l3 3 6-7" fill="none" stroke="#5a8f8a" stroke-width="2"/></svg><div class="txt"><h4>Vulputate Molestie Consequat</h4><p>quis nostrud exetiperj saliquip commodr consequa uisquis nostru iexetip suscipitt lobtis nisl ut aliquip exea commod</p></div></div>
    <span class="link" style="left:150px;top:204px">KNOW MORE</span>
  </div>

  <div class="abs card" style="left:573px">
    <span class="icon"></span>
    <svg class="abs" style="left:17px;top:17px" width="14" height="14" viewBox="0 0 14 14"><ellipse cx="7" cy="6" rx="6" ry="4.5" fill="none" stroke="#fff" stroke-width="1.5"/></svg>
    <h3>TESTIMONIALS</h3>
    <div class="avatar" role="img" aria-label="Portrait photo of the client"></div>
    <div class="person"><b>Marek Olsted</b><small>Bussiness Man</small></div>
    <div class="quote">“ Ut wisi enim ad minim veniam, quism nostrli erci tation ullamcorper suscipitop lobortis commodo ” consequat.
      <div class="qdots"><span></span><span class="on"></span><span></span><span></span></div></div>
  </div>
</section>

<section>
  <div class="abs types"></div>
  <svg class="abs types-tab" width="176" height="24" viewBox="0 0 176 24"><path d="M0 0H176L166 24H10Z" fill="#d9302a"/></svg>
  <h2 class="abs types-title">BUILDING TYPES</h2>
  <svg class="abs arrow" style="left:78px" width="10" height="18" viewBox="0 0 10 18"><path d="M9 1L1 9l8 8" fill="none" stroke="#aaa" stroke-width="2"/></svg>
  <div class="abs tile" style="left:97px;background:linear-gradient(180deg,#c9ccce,#a79b86 60%,#8a8c7a)" role="img" aria-label="Photo of a farm shop building"><div class="label">Farm Shops</div></div>
  <div class="abs tile" style="left:271px;background:linear-gradient(180deg,#8fb6d6,#7a8690 55%,#cfc7b4)" role="img" aria-label="Photo of a machine storage building"><div class="label">Machine Storage</div></div>
  <div class="abs tile" style="left:445px;background:linear-gradient(180deg,#d2dce2,#b9bfc0 55%,#7c8a6e)" role="img" aria-label="Photo of a seed dealership with grain bins"><div class="label">Seed Dealership</div></div>
  <div class="abs tile" style="left:618px;background:linear-gradient(180deg,#9bb8c9,#6f9a4a 45%,#c9a76a)" role="img" aria-label="Aerial photo of a dairy barn"><div class="label">Dairy</div></div>
  <svg class="abs arrow" style="left:794px" width="10" height="18" viewBox="0 0 10 18"><path d="M1 1l8 8-8 8" fill="none" stroke="#888" stroke-width="2"/></svg>
</section>

<footer>
  <div class="abs footer"></div>
  <div class="abs footer-brand">Brenwick Structures</div>
  <ul class="abs footer-nav"><li>HOME</li><li>PORTFOLIO</li><li>PRODUCT SPACS</li><li>TESTIMONIALS</li><li>OUR PROCESS</li><li>CONTACT US</li></ul>
  <div class="abs copy">Copyright © 2015 Brenwick Structures &nbsp;| &nbsp;All Rights Reserved</div>
  <div class="abs bottom-rule"></div>
</footer>
</body>
</html>
```